business card for a massage therapy practice named 'Cedar and Willow Massage Studio'

I really need a trendy, yet easy on the eyes business card to complement my logo. Ideally with some gold or rose gold foil work.

My uploaded file of the logo I have in horizontal but I have a vertical version as well. Another color that is used in the website is a blush pink here and there. I'd like to see some trendy tropical leaves in the design.

```html
<!DOCTYPE html>
<html lang="en">
<head>
<meta charset="utf-8">
<title>Cedar and Willow Massage Studio – Business Card</title>
<link rel="stylesheet" href="https://fonts.googleapis.com/css2?family=Open+Sans:wght@400&display=swap">
<style>
  :root {
    --backdrop: #2f2f30;
    --card-white: #ffffff;
    --ink: #2a2a2a;
    --mint: #6fd0b5;
    --gold: #a8915f;
    --rule: #c9c9c9;
    --back-base: #8f7b58;
    --back-light: #a9987a;
  }
  * { margin: 0; padding: 0; box-sizing: border-box; }
  html, body {
    width: 1200px; height: 802px; overflow: hidden;
    background: var(--backdrop);
    font-family: "Open Sans", Arial, sans-serif;
  }
  .canvas { position: relative; width: 1200px; height: 802px; }
  .card {
    position: absolute; top: 274px; width: 443px; height: 265px;
    box-shadow: 0 4px 10px rgba(0,0,0,.45);
  }
  .card--front { left: 136px; background: var(--card-white); color: var(--ink); }
  .card--back {
    left: 624px;
    background: radial-gradient(circle at 50% 50%, var(--back-light) 0%, var(--back-base) 70%);
  }
  .brand {
    position: absolute; left: 22px; top: 46px;
    display: flex; align-items: center; gap: 12px;
  }
  .brand__mark { width: 40px; height: 40px; border-radius: 50%; background: var(--gold); flex: none; }
  .brand__name {
    font-size: 19px; line-height: 1.2; color: var(--ink); font-weight: 400;
  }
  .person { position: absolute; left: 24px; top: 157px; right: 30px; }
  .person__name { font-size: 16px; color: var(--mint); letter-spacing: .2px; line-height: 1.2; }
  .person__role-row { display: flex; align-items: center; gap: 6px; }
  .person__role { font-size: 12.5px; line-height: 1.3; white-space: nowrap; }
  .person__rule { flex: 1; height: 1px; background: var(--rule); margin-top: 5px; }
  .contact {
    position: absolute; left: 24px; right: 29px; top: 209px;
    display: flex; justify-content: space-between; font-size: 12.5px; line-height: 16px;
  }
  .contact__line { display: flex; align-items: center; gap: 5px; }
  .contact__line svg { width: 11px; height: 11px; fill: var(--mint); flex: none; }
  .contact__address { text-align: right; }
</style>
</head>
<body>
<main class="canvas">
  <section class="card card--front">
    <div class="brand">
      <span class="brand__mark"></span>
      <span class="brand__name">Cedar and Willow<br>Massage Studio</span>
    </div>

    <div class="person">
      <p class="person__name">MARISOL VEGA</p>
      <div class="person__role-row">
        <span class="person__role">Massage Therapist</span>
        <span class="person__rule"></span>
      </div>
    </div>

    <div class="contact">
      <div class="contact__lines">
        <p class="contact__line">
          <svg viewBox="0 0 24 24" aria-hidden="true"><path d="M6.6 10.8a15 15 0 0 0 6.6 6.6l2.2-2.2a1 1 0 0 1 1-.25 11.4 11.4 0 0 0 3.6.6 1 1 0 0 1 1 1V20a1 1 0 0 1-1 1A17 17 0 0 1 3 4a1 1 0 0 1 1-1h3.5a1 1 0 0 1 1 1c0 1.25.2 2.45.6 3.6a1 1 0 0 1-.25 1z"/></svg>
          (916) 555-0148
        </p>
        <p class="contact__line">
          <svg viewBox="0 0 24 24" aria-hidden="true"><path d="M2 5h20v14H2z M2 5l10 8 10-8" fill="none" stroke="currentColor"/><path d="M2 5h20v2l-10 7L2 7z M2 9l10 7 10-7v10H2z"/></svg>
          hello@cedarandwillow.com
        </p>
      </div>
      <div class="contact__address">
        <p>418 Laurel St. suite 210</p>
        <p>Fairhaven, CA 95820</p>
      </div>
    </div>
  </section>

  <section class="card card--back" role="img" aria-label="Repeating pattern of pale pineapple illustrations on a warm gold-brown ground"></section>
</main>
</body>
</html>
```